Presentation Box for dry goods meat product

We would like a box designed for presentation on a shelf. Our product is fully cooked meats (beef, pork and chicken) that has a 12- to 18-month shelf-life without refrigeration. It's not dried food, but because of the cooking process it's succulent meat in sauce, storable at room temperature.Our anchor product will be "Timber Hollow Smoke Pot."The dimensions for the box will be approximately 8" tall by 5" wide and 2.5" deep.We have an oval-shaped (horizontal) logo in Navy, Crimson and Old Gold (think Dunmore Lanterns colors).
Updates

Reason: We haven't received enough options. We want the design to say "Timber Hollow Style Smoke Pot" not "Timber Hollow Smoke Pot." Use pictures of beef brisket (not steaks), pulled pork (not pork chops) and pulled chicken (not chicken legs/thighs).

Target Market(s)

Meat-buying consumers

Industry/Entity Type

Cooking

Requirements
Must have
• Space for ingredients and nutrition information. The name of our company is Merrow Foods.
Nice to have
• Picture of Bar-B-Que beef, pork and chicken

```html
<!DOCTYPE html>
<html lang="en">
<head>
<meta charset="utf-8">
<title>Merrow Foods – Timber Hollow Style Smoke Pot Box</title>
<link rel="stylesheet" href="https://fonts.googleapis.com/css2?family=Open+Sans:wght@600;700&family=Nunito+Sans:wght@800&family=Baloo+2:wght@600&family=Great+Vibes&display=swap">
<style>
  :root {
    --page-bg: #ececec;
    --red: #d41f2a;
    --red-dark: #b5141f;
    --red-stripe: #c3121d;
    --pink: #f3c9cf;
    --white: #ffffff;
    --navy: #1c2350;
    --maroon: #8a1732;
    --orange: #f2941f;
    --orange-edge: #fbe3b9;
    --title-text: #fff6ee;
    --rule: #4a4a4a;
    --ink: #222222;
    --food-dark: #6a3a1e;
    --food-warm: #c9542a;
    --food-yellow: #f0b42a;
    --plate: #f4f1ee;
  }
  * { box-sizing: border-box; margin: 0; padding: 0; }
  html, body { width: 1079px; height: 1200px; overflow: hidden; background: var(--page-bg); }
  .dieline {
    position: absolute; left: 165px; top: 200px;
    display: flex; height: 800px;
    box-shadow: 0 10px 30px rgba(0,0,0,.18);
  }
  .panel { position: relative; height: 100%; overflow: hidden; }
  .striped {
    background: repeating-linear-gradient(90deg, var(--red) 0 5px, var(--red-stripe) 5px 8px);
  }

  /* Front panel */
  .front { width: 500px; }
  .front .brand-area {
    position: absolute; inset: 0 0 auto 0; height: 300px;
    background: linear-gradient(180deg, var(--white) 0 70%, var(--pink) 100%);
    border-radius: 0 0 50% 50% / 0 0 22% 22%;
    display: flex; flex-direction: column; align-items: center; justify-content: center;
    padding-bottom: 30px;
  }
  .brand-name {
    font-family: "Nunito Sans", sans-serif; font-weight: 800;
    color: var(--navy); font-size: 64px; line-height: 1; letter-spacing: -1px;
  }
  .brand-sub {
    font-family: "Nunito Sans", sans-serif; font-weight: 800;
    color: var(--navy); font-size: 26px; letter-spacing: 1px; margin-top: 4px; align-self: flex-end; margin-right: 130px;
  }
  .fabric {
    position: absolute; left: 0; right: 0; top: 330px; height: 230px;
    background: radial-gradient(ellipse at 40% 50%, #e63a3f 0%, var(--red-dark) 60%, #8f0d16 100%);
    opacity: .85;
  }
  .title-block { position: absolute; left: 30px; right: 22px; top: 325px; }
  .style-tag {
    display: block; width: max-content; margin: 0 auto;
    background: var(--maroon); color: var(--white);
    font-family: "Open Sans", sans-serif; font-weight: 700; font-size: 24px;
    padding: 4px 12px; border: 2px solid var(--white); position: relative; z-index: 2;
  }
  .product-banner {
    margin-top: -6px; background: var(--orange); border: 2px solid var(--orange-edge);
    text-align: center; padding: 6px 0 2px;
  }
  .product-name {
    font-family: "Baloo 2", sans-serif; font-weight: 600; font-size: 62px; line-height: 1.1;
    color: var(--title-text); text-shadow: 2px 2px 3px rgba(90,30,0,.55);
  }
  .variant-tab {
    display: block; width: 150px; margin: 0 auto;
    background: var(--navy); color: var(--white); text-align: center;
    font-family: "Great Vibes", cursive; font-size: 28px; line-height: 1.3;
    border-radius: 0 0 14px 14px; border: 2px solid var(--white); border-top: 0;
  }
  .front .food-photo {
    position: absolute; left: 0; right: 0; bottom: 30px; height: 260px;
    background: radial-gradient(ellipse at 35% 55%, var(--food-dark) 0 30%, transparent 45%),
                radial-gradient(ellipse at 78% 55%, var(--food-yellow) 0 15%, var(--food-warm) 25%, transparent 40%),
                linear-gradient(180deg, #e8d8d0 0%, var(--plate) 40%, #e7e0dc 100%);
    border-radius: 40px 40px 0 0;
  }
  .front .bottom-band { position: absolute; left: 0; right: 0; bottom: 0; height: 30px; }

  /* Side panel */
  .side { width: 250px; }
  .side .side-title { position: absolute; left: 14px; right: 14px; top: 80px; }
  .side .style-tag { font-size: 14px; padding: 2px 8px; }
  .side .product-banner { padding: 2px 0 0; }
  .side .product-name { font-size: 34px; }
  .side .variant-tab { width: 80px; font-size: 17px; border-radius: 0 0 9px 9px; }
  .info-sheet {
    position: absolute; left: 12px; right: 12px; top: 200px; bottom: 0;
    background: linear-gradient(180deg, var(--white) 0 72%, rgba(255,255,255,.6) 100%);
    padding: 30px 16px 0 16px;
  }
  .info-heading {
    font-family: "Open Sans", sans-serif; font-weight: 600; font-size: 14px; color: var(--ink);
    margin-bottom: 10px;
  }
  .info-lines { list-style: none; margin-bottom: 36px; }
  .info-lines li { height: 14px; border-bottom: 1px solid var(--rule); }
  .side .food-photo {
    position: absolute; left: 0; right: 0; bottom: 30px; height: 200px;
    background: radial-gradient(ellipse at 35% 60%, var(--food-dark) 0 30%, transparent 48%),
                radial-gradient(ellipse at 85% 45%, var(--food-yellow) 0 15%, var(--food-warm) 28%, transparent 42%),
                linear-gradient(180deg, #efe4de, var(--plate));
  }
  .side .bottom-band { position: absolute; left: 0; right: 0; bottom: 0; height: 30px; }
</style>
</head>
<body>
  <main class="dieline">
    <section class="panel front striped">
      <header class="brand-area">
        <span class="brand-name">Merrow</span>
        <span class="brand-sub">Foods</span>
      </header>
      <div class="fabric" role="img" aria-label="Draped red satin backdrop"></div>
      <div class="title-block">
        <span class="style-tag">Timber Hollow Style</span>
        <div class="product-banner"><span class="product-name">Smoke Pot</span></div>
        <span class="variant-tab">Beef</span>
      </div>
      <div class="food-photo" role="img" aria-label="Plate of barbecued beef with grilled peppers, tomatoes, greens and two glasses of white wine"></div>
      <div class="bottom-band striped"></div>
    </section>

    <aside class="panel side striped">
      <div class="side-title title-block">
        <span class="style-tag">Timber Hollow Style</span>
        <div class="product-banner"><span class="product-name">Smoke Pot</span></div>
        <span class="variant-tab">Beef</span>
      </div>
      <div class="info-sheet">
        <h2 class="info-heading">Nutrition information</h2>
        <ul class="info-lines"><li></li><li></li><li></li><li></li><li></li><li></li><li></li><li></li></ul>
        <h2 class="info-heading">Ingredients</h2>
        <ul class="info-lines"><li></li><li></li><li></li><li></li><li></li><li></li></ul>
      </div>
      <div class="food-photo" role="img" aria-label="Barbecued beef with grilled peppers and greens"></div>
      <div class="bottom-band striped"></div>
    </aside>
  </main>
</body>
</html>
```